Business Card For Halvenmoor Financial Consulting

Hi, I would like a business card designed. Bold, modern.
Please use the same design as the logo. I have also attached the website design to see the overall theme.
Wordmark Font
Color: Hex: #01AEF7

```html
<!DOCTYPE html>
<html lang="en">
<head>
<meta charset="utf-8">
<title>Halvenmoor Financial Consulting – Business Card</title>
<link rel="stylesheet" href="https://fonts.googleapis.com/css2?family=Montserrat:wght@700&family=Open+Sans:wght@400;700&display=swap">
<style>
  :root {
    --backdrop: #222222;
    --navy: #0b4468;
    --navy-light: #1d5c86;
    --brand-blue: #01aef7;
    --name-blue: #2a9fdc;
    --ink: #1a1a1a;
    --paper: #ffffff;
    --divider: #1e4f78;
  }
  * { margin: 0; padding: 0; box-sizing: border-box; }
  html, body { width: 1200px; height: 780px; overflow: hidden; background: var(--backdrop); }
  .canvas {
    width: 1200px; height: 780px;
    display: flex; align-items: center; justify-content: center; gap: 40px;
  }
  .card {
    width: 540px; height: 309px; position: relative; overflow: hidden;
    box-shadow: 0 10px 30px rgba(0,0,0,.5);
  }
  /* Front */
  .card-front {
    background: linear-gradient(115deg, var(--navy-light) 0%, var(--navy) 45%, var(--navy) 70%, #135580 100%);
    display: flex; align-items: center; justify-content: center;
  }
  .front-band {
    position: absolute; top: 0; right: 60px; width: 150px; height: 100%;
    background: rgba(255,255,255,.05);
  }
  .front-brand { display: flex; align-items: center; gap: 16px; position: relative; }
  .brand-square {
    width: 46px; height: 46px; border: 4px solid var(--brand-blue); flex: none;
  }
  .front-brand .brand-name {
    font-family: "Montserrat", sans-serif; font-weight: 700; color: var(--paper);
    font-size: 30px; line-height: 1.05; letter-spacing: 1px; text-transform: uppercase;
  }
  .brand-name span { display: block; }
  .front-brand .brand-name span + span { font-size: 14px; letter-spacing: 5px; margin-top: 6px; }
  /* Back */
  .card-back { background: var(--paper); display: flex; align-items: center; padding: 0 30px; }
  .back-brand { display: flex; align-items: center; gap: 10px; width: 210px; }
  .back-brand .brand-square { width: 30px; height: 30px; border-width: 3px; }
  .back-brand .brand-name {
    font-family: "Montserrat", sans-serif; font-weight: 700; color: var(--navy);
    font-size: 20px; line-height: 1.1; text-transform: uppercase; letter-spacing: .5px;
  }
  .back-brand .brand-name span + span { font-size: 9px; letter-spacing: 2.5px; margin-top: 4px; }
  .divider { width: 1px; height: 150px; background: var(--divider); margin: 0 24px 0 8px; }
  .contact { font-family: "Open Sans", sans-serif; color: var(--ink); }
  .person-name { font-weight: 700; color: var(--name-blue); font-size: 22px; line-height: 1.1; }
  .person-role { font-size: 12.5px; margin-bottom: 12px; }
  .address { font-size: 12.5px; line-height: 1.35; margin-bottom: 10px; }
  .contact-list { list-style: none; font-size: 12.5px; line-height: 1.6; }
  .contact-list li { display: flex; align-items: center; gap: 8px; }
  .contact-list svg { width: 13px; height: 13px; fill: none; stroke: var(--name-blue); stroke-width: 2; }
</style>
</head>
<body>
<main class="canvas">
  <section class="card card-front" aria-label="Card front">
    <div class="front-band"></div>
    <div class="front-brand">
      <div class="brand-square"></div>
      <div class="brand-name"><span>Halvenmoor</span><span>Financial Consulting</span></div>
    </div>
  </section>

  <section class="card card-back" aria-label="Card back">
    <div class="back-brand">
      <div class="brand-square"></div>
      <div class="brand-name"><span>Halvenmoor</span><span>Financial Consulting</span></div>
    </div>
    <div class="divider"></div>
    <div class="contact">
      <p class="person-name">Marta Vellandrova</p>
      <p class="person-role">Managing Director</p>
      <p class="address">1840 Larkfield Ave. Suite 310<br>Dayton, OH 45402</p>
      <ul class="contact-list">
        <li><svg viewBox="0 0 24 24"><path d="M5 3h4l2 5-3 2a12 12 0 0 0 6 6l2-3 5 2v4a2 2 0 0 1-2 2A17 17 0 0 1 3 5a2 2 0 0 1 2-2z"/></svg>(937) 555-0184</li>
        <li><svg viewBox="0 0 24 24"><rect x="3" y="5" width="18" height="14"/><path d="M3 6l9 7 9-7"/></svg>info@halvenmoor.com</li>
        <li><svg viewBox="0 0 24 24"><circle cx="12" cy="12" r="9"/><path d="M3 12h18M12 3c3 3 3 15 0 18M12 3c-3 3-3 15 0 18"/></svg>www.halvenmoor.com</li>
      </ul>
    </div>
  </section>
</main>
</body>
</html>
```